I would like a simple but elegant desing that is eye catching. I design floral arrangements for all types of parties, and sew mariachi trajes (outfits). I would like somehow to combine floral and mariachi together or a design that indicates Fiesta/party. Disregard color any color will be fine to match simplicity of design.

Target Market(s)

Adults and teenagers

Industry/Entity Type

Floral

Contact Information for Business Card

"Garden Lantern"
Specializing on floral designs for all ocassions
Contact Marla Benitez
(210) 555-0173
We have the connections to meet all your party needs..
E-mail: velardobenitezmarisol@mailpost.example

Font styles to use
Decorative
Script

Colors

Designer to choose colors to be used in the design.

Requirements
Must have
• Simple, eye catching
Nice to have
• Logo could have a mariachi hat with light floral background or could be simply an abstract design

```html
<!DOCTYPE html>
<html lang="en">
<head>
<meta charset="utf-8">
<title>Garden Lantern – Business Card</title>
<link rel="stylesheet" href="https://fonts.googleapis.com/css2?family=Michroma&family=Carlito:wght@400;700&display=swap">
<style>
  :root {
    --backdrop: #e9e6e1;
    --card: #ffffff;
    --brand-blue: #00aeef;
    --on-blue: #ffffff;
    --gap: 7px;
  }
  * { margin: 0; padding: 0; box-sizing: border-box; }
  html, body {
    width: 1200px; height: 959px; overflow: hidden;
    background: var(--backdrop);
  }
  .card {
    position: absolute;
    left: 100px; top: 194px;
    width: 1000px; height: 571px;
    background: var(--card);
    box-shadow: 0 6px 24px rgba(0,0,0,0.12);
    overflow: hidden;
  }
  .top-strip {
    position: absolute; left: 0; right: 0; top: 0; height: 16px;
    display: grid; grid-template-columns: repeat(3, 1fr); gap: 5px;
  }
  .top-strip span { background: var(--brand-blue); }
  .company {
    position: absolute; left: 0; right: 0; top: 100px;
    text-align: center;
    font-family: "Michroma", sans-serif;
    font-weight: 400;
    font-variant: small-caps;
    font-size: 44px; letter-spacing: 5px;
    color: var(--brand-blue);
  }
  .person {
    position: absolute; left: 0; right: 0; top: 205px;
    text-align: center;
    font-family: "Carlito", sans-serif;
    color: var(--brand-blue);
  }
  .person .name { font-size: 36px; letter-spacing: 0.5px; line-height: 1.1; }
  .person .role { font-size: 26px; line-height: 1.2; }
  .contact-row {
    position: absolute; left: 0; right: 0; bottom: 0; height: 240px;
    display: grid; grid-template-columns: repeat(3, 1fr); gap: var(--gap);
  }
  .contact-box {
    background: var(--brand-blue);
    color: var(--on-blue);
    font-family: "Carlito", sans-serif;
    font-size: 20px; line-height: 1.35;
    text-align: center;
    padding-top: 50px;
    white-space: nowrap;
  }
  .contact-box svg { display: block; margin: 0 auto 26px; }
</style>
</head>
<body>
  <main class="card">
    <div class="top-strip"><span></span><span></span><span></span></div>

    <h1 class="company">Garden Lantern</h1>

    <div class="person">
      <p class="name">DALIA FERRAND</p>
      <p class="role">GENERAL MANAGER</p>
    </div>

    <section class="contact-row">
      <div class="contact-box phone">
        <svg width="60" height="60" viewBox="0 0 60 60" aria-hidden="true">
          <circle cx="30" cy="30" r="27" fill="none" stroke="#fff" stroke-width="2.5"/>
          <path d="M22 17c2-1 3 0 4 2l2 5c0 2-1 3-3 4 1 4 4 7 8 8 1-2 2-3 4-3l5 2c2 1 3 2 2 4-1 3-4 4-7 4-10-1-18-9-19-19 0-3 1-6 4-7z" fill="#fff"/>
        </svg>
        <p>(555) 014 2290</p>
        <p>(555) 014 2291</p>
      </div>
      <div class="contact-box address">
        <svg width="60" height="60" viewBox="0 0 60 60" aria-hidden="true">
          <circle cx="30" cy="30" r="27" fill="none" stroke="#fff" stroke-width="2.5"/>
          <path d="M30 14c-6 0-11 5-11 11 0 8 11 21 11 21s11-13 11-21c0-6-5-11-11-11z" fill="#fff"/>
          <circle cx="30" cy="25" r="4.5" fill="var(--brand-blue)"/>
        </svg>
        <p>Alder Row, No. 27</p>
        <p>Brookvale, Westmere</p>
      </div>
      <div class="contact-box web">
        <svg width="60" height="60" viewBox="0 0 60 60" aria-hidden="true">
          <circle cx="30" cy="30" r="27" fill="none" stroke="#fff" stroke-width="2.5"/>
          <g fill="none" stroke="#fff" stroke-width="2">
            <circle cx="30" cy="30" r="15"/>
            <ellipse cx="30" cy="30" rx="7" ry="15"/>
            <line x1="15" y1="30" x2="45" y2="30"/>
            <path d="M17 22h26M17 38h26"/>
          </g>
        </svg>
        <p>info@gardenlantern.example</p>
        <p>www.gardenlantern.example</p>
      </div>
    </section>
  </main>
</body>
</html>
```